Brackwell Yard Services Flyer Design

I need a new flyer design for my business, Brackwell Yard Services. I’ll be providing my old flyer and logo as references. The new flyer should feature updated wording, contact information, logos, and photos, but still keep the original “What We Do” section and include the phrase “Don’t See? Just Ask!” somewhere near the services. The flyer needs to look great in black and white for door-to-door handouts but also be eye-catching and professional enough for social media use.

The updated content should include the headline “Transforming Outdoor Spaces with Hard Work & Precision” and highlight three main service areas: Landscaping Services (project-based landscaping to clean, prepare, and transform outdoor spaces with precision), Property Cleanup (quick hauls, debris removal, or full cleanouts—no job too big or small), and Ground Preparation (pad preparation, brush removal, and fire lines—making properties safe, functional, and project-ready).

Please also include a “Why Choose Us?” section that lists: Locally owned since 2022, Reliable & affordable – no corners cut, Professional results you can trust, LICENSED AND Insured, and Quality work / on time / references / flexible / follow-up.

At the bottom, include the contact details: Call or Text Today!
www.brackwellyard.example
| sales@brackwellyard.example
| (555) 014-7293

The overall design should be clean, professional, and easy to read with a layout that clearly shows what we offer. Use visuals that represent outdoor services, landscaping, and property cleanup/prep work. I want something that feels trustworthy, family-friendly, and modern.
Use the same photo of leaf clean up from the original flyer if possible.
Our company colors are also black and white. For the most part.

```html
<!DOCTYPE html>
<html lang="en">
<head>
<meta charset="utf-8">
<title>Brackwell Yard Services Flyer</title>
<link rel="stylesheet" href="https://fonts.googleapis.com/css2?family=Oswald:wght@500;600;700&family=Fira+Sans+Condensed:wght@600&family=Source+Sans+3:wght@400;600;700&display=swap">
<style>
  :root {
    --orange: #f39322;
    --black: #0b0b0b;
    --white: #ffffff;
    --ink: #1c1c1c;
    --hero-warm: linear-gradient(180deg, #2f3a1c 0%, #5d6a2c 35%, #9a5a24 62%, #6b3a18 80%, #2a2410 100%);
    --hero-gray: linear-gradient(180deg, #2a2a2a 0%, #6a6a6a 35%, #8a8a8a 62%, #555 80%, #1e1e1e 100%);
  }
  * { box-sizing: border-box; margin: 0; padding: 0; }
  html, body { width: 1200px; height: 765px; overflow: hidden; background: var(--white); }
  body { position: relative; font-family: "Source Sans 3", Arial, sans-serif; color: var(--ink); }

  .flyer {
    position: absolute; top: 0; width: 593px; height: 765px; overflow: hidden;
    background: var(--white);
  }
  .flyer--color {
    left: 0;
    --accent: var(--orange); --label-bg: var(--orange); --label-text: var(--white);
    --band: var(--orange); --band-label-bg: var(--white); --band-label-text: var(--orange);
    --band-ask: #2a1a08; --bullet: var(--orange); --footer-text: var(--orange);
    --hero: var(--hero-warm);
  }
  .flyer--mono {
    left: 607px;
    --accent: var(--black); --label-bg: var(--black); --label-text: var(--white);
    --band: var(--black); --band-label-bg: var(--white); --band-label-text: var(--black);
    --band-ask: var(--white); --bullet: var(--black); --footer-text: var(--white);
    --hero: var(--hero-gray);
    filter: grayscale(1);
  }

  .hero { position: absolute; left: 0; top: 0; width: 593px; height: 183px; background: var(--hero); }
  .hero::after { content: ""; position: absolute; inset: 0; background: linear-gradient(180deg, rgba(0,0,0,0) 55%, rgba(0,0,0,.55) 100%); }
  .brand {
    position: absolute; right: 14px; top: 10px; z-index: 2;
    display: flex; align-items: center; gap: 6px;
    font-family: "Oswald", sans-serif; font-weight: 700; font-size: 15px; line-height: 1.05;
    color: var(--white); text-transform: uppercase; text-align: right;
  }
  .brand__mark { width: 12px; height: 12px; background: var(--white); }
  .headline {
    position: absolute; left: 9px; top: 133px; z-index: 2;
    font-family: "Oswald", sans-serif; font-weight: 700; font-size: 20px; line-height: 23px;
    color: var(--white); text-transform: uppercase; text-align: center; letter-spacing: -.2px;
  }

  .label {
    position: absolute; font-family: "Fira Sans Condensed", sans-serif; font-weight: 600;
    font-size: 22px; line-height: 1; display: flex; align-items: center; justify-content: center;
  }
  .label--services { left: 231px; top: 198px; width: 130px; height: 32px; background: var(--label-bg); color: var(--label-text); }
  .label--work { left: 232px; top: 338px; width: 128px; height: 31px; background: var(--band-label-bg); color: var(--band-label-text); }
  .label--why { left: 380px; top: 545px; width: 175px; height: 32px; background: var(--label-bg); color: var(--label-text); }

  .service { position: absolute; top: 243px; }
  .service__title { font-family: "Oswald", sans-serif; font-weight: 500; font-size: 19px; color: var(--accent); text-transform: uppercase; line-height: 24px; letter-spacing: -.2px; }
  .service__text { font-size: 11.6px; line-height: 14px; margin-top: 5px; color: var(--ink); }

  .band { position: absolute; left: 0; top: 323px; width: 593px; height: 197px; background: var(--band); }
  .task { position: absolute; top: 384px; color: var(--white); }
  .task__title { font-family: "Oswald", sans-serif; font-weight: 500; font-size: 19px; line-height: 24px; text-transform: uppercase; letter-spacing: -.2px; }
  .task__list { list-style: none; margin-top: 6px; }
  .task__list li { display: flex; align-items: center; gap: 6px; font-size: 12.5px; height: 19.4px; }
  .hex { width: 11px; height: 10px; flex: none; clip-path: polygon(25% 0,75% 0,100% 50%,75% 100%,25% 100%,0 50%); }
  .task .hex { background: var(--white); }
  .ask {
    position: absolute; left: 0; width: 593px; top: 492px; text-align: center;
    font-family: "Oswald", sans-serif; font-weight: 600; font-size: 16px; color: var(--band-ask); letter-spacing: -.3px;
  }

  .photo { position: absolute; top: 534px; width: 119px; height: 119px; }
  .photo--haul { left: 2px; background: linear-gradient(160deg, #4b5a3a, #8a7a60 55%, #5e4a34); }
  .photo--rake { left: 124px; background: linear-gradient(160deg, #5a6a40, #8d6a3a 60%, #b07a3e); }
  .photo--saw { left: 247px; background: linear-gradient(160deg, #3e4a30, #7a6a50 55%, #c7a27a); }

  .why { position: absolute; left: 382px; top: 588px; list-style: none; }
  .why li { display: flex; align-items: center; gap: 6px; font-size: 11.6px; height: 19.4px; }
  .why .hex, .perks .dot { background: var(--bullet); }

  .licensed { position: absolute; left: 0; width: 593px; top: 665px; text-align: center; font-family: "Oswald", sans-serif; font-weight: 500; font-size: 17px; color: var(--accent); text-transform: uppercase; letter-spacing: -.3px; }
  .perks { position: absolute; left: 0; width: 593px; top: 688px; display: flex; justify-content: center; align-items: center; gap: 4px; font-size: 11.6px; }
  .perks .dot { width: 4px; height: 4px; border-radius: 50%; }

  .footer { position: absolute; left: 0; top: 715px; width: 593px; height: 50px; background: var(--black); color: var(--footer-text); text-align: center; }
  .footer__cta { font-family: "Oswald", sans-serif; font-weight: 600; font-size: 19px; line-height: 1; padding-top: 4px; text-transform: uppercase; }
  .contacts { display: flex; justify-content: center; gap: 14px; margin-top: 3px; font-weight: 700; font-size: 13.4px; }
  .contact { display: flex; align-items: center; gap: 4px; }
  .contact svg { width: 14px; height: 14px; stroke: var(--footer-text); fill: none; stroke-width: 1.4; }
</style>
</head>
<body>
  <section class="flyer flyer--color">
    <div class="hero" role="img" aria-label="Photo of a large pile of autumn leaves raked on a green lawn beside a tree"></div>
    <div class="brand"><span>Brackwell Yard<br>Services</span><span class="brand__mark"></span></div>
    <h1 class="headline">Transforming Outdoor Spaces<br>with Hard Work &amp; Precision</h1>

    <h2 class="label label--services">Our Services</h2>
    <div class="service" style="left:20px"><h3 class="service__title">Landscaping Services</h3><p class="service__text">Project-based landscaping to<br>clean, prepare, and transform<br>outdoor spaces with precision.</p></div>
    <div class="service" style="left:215px"><h3 class="service__title">Ground Preparation</h3><p class="service__text">Pad preparation, brush removal,<br>and fire lines—making properties<br>safe, functional, and project-ready.</p></div>
    <div class="service" style="left:402px"><h3 class="service__title">Property Cleanup</h3><p class="service__text">Quick hauls, debris removal, or full<br>cleanouts—no job too big or small.</p></div>

    <div class="band"></div>
    <h2 class="label label--work">What We Do</h2>
    <div class="task" style="left:43px"><h3 class="task__title">Remove</h3><ul class="task__list"><li><span class="hex"></span>Junk removal</li><li><span class="hex"></span>Trash &amp; waste hauling</li><li><span class="hex"></span>Yard &amp; garden cleanup</li><li><span class="hex"></span>Appliance removal</li></ul></div>
    <div class="task" style="left:229px"><h3 class="task__title">Install</h3><ul class="task__list"><li><span class="hex"></span>Mulch</li><li><span class="hex"></span>DG</li><li><span class="hex"></span>Plants</li><li><span class="hex"></span>Rock</li></ul></div>
    <div class="task" style="left:359px"><h3 class="task__title">Maintenance &amp; Other</h3><ul class="task__list"><li><span class="hex"></span>Yard cleanup</li><li><span class="hex"></span>Weed prevention (pre-emergent)</li><li><span class="hex"></span>Roof &amp; gutter cleaning</li><li><span class="hex"></span>Fence &amp; deck staining</li></ul></div>
    <p class="ask">DON’T SEE? JUST ASK!</p>

    <div class="photo photo--haul" role="img" aria-label="Photo of a worker hauling brush in a wheelbarrow"></div>
    <div class="photo photo--rake" role="img" aria-label="Photo of a rake gathering fallen leaves on grass"></div>
    <div class="photo photo--saw" role="img" aria-label="Photo of a worker cutting a fallen branch with a chainsaw"></div>

    <h2 class="label label--why">Why Choose Us?</h2>
    <ul class="why"><li><span class="hex"></span>Locally owned since 2022</li><li><span class="hex"></span>Reliable &amp; affordable – no corners cut</li><li><span class="hex"></span>Professional results you can trust</li></ul>

    <p class="licensed">Licensed and Insured</p>
    <p class="perks">Quality work <span class="dot"></span> On Time <span class="dot"></span> References <span class="dot"></span> Flexible <span class="dot"></span> Follow-up</p>

    <footer class="footer">
      <p class="footer__cta">Call or Text Today!</p>
      <div class="contacts">
        <span class="contact"><svg viewBox="0 0 16 16"><circle cx="8" cy="8" r="6.5"/><ellipse cx="8" cy="8" rx="3" ry="6.5"/><path d="M1.5 8h13M2.5 4.5h11M2.5 11.5h11"/></svg>www.brackwellyard.example</span>
        <span class="contact"><svg viewBox="0 0 16 16"><rect x="1.5" y="3.5" width="13" height="9"/><path d="M1.5 3.5 8 9l6.5-5.5"/></svg>sales@brackwellyard.example</span>
        <span class="contact"><svg viewBox="0 0 16 16"><path d="M4 1.5 6 4.5 4.8 6a8 8 0 0 0 5.2 5.2L11.5 10l3 2-1.5 2.2C7.5 14 2 8.5 1.8 3z"/></svg>(555) 014-7293</span>
      </div>
    </footer>
  </section>

  <section class="flyer flyer--mono">
    <div class="hero" role="img" aria-label="Black and white photo of a large pile of autumn leaves raked on a lawn beside a tree"></div>
    <div class="brand"><span>Brackwell Yard<br>Services</span><span class="brand__mark"></span></div>
    <h1 class="headline">Transforming Outdoor Spaces<br>with Hard Work &amp; Precision</h1>

    <h2 class="label label--services">Our Services</h2>
    <div class="service" style="left:20px"><h3 class="service__title">Landscaping Services</h3><p class="service__text">Project-based landscaping to<br>clean, prepare, and transform<br>outdoor spaces with precision.</p></div>
    <div class="service" style="left:215px"><h3 class="service__title">Ground Preparation</h3><p class="service__text">Pad preparation, brush removal,<br>and fire lines—making properties<br>safe, functional, and project-ready.</p></div>
    <div class="service" style="left:402px"><h3 class="service__title">Property Cleanup</h3><p class="service__text">Quick hauls, debris removal, or full<br>cleanouts—no job too big or small.</p></div>

    <div class="band"></div>
    <h2 class="label label--work">What We Do</h2>
    <div class="task" style="left:43px"><h3 class="task__title">Remove</h3><ul class="task__list"><li><span class="hex"></span>Junk removal</li><li><span class="hex"></span>Trash &amp; waste hauling</li><li><span class="hex"></span>Yard &amp; garden cleanup</li><li><span class="hex"></span>Appliance removal</li></ul></div>
    <div class="task" style="left:229px"><h3 class="task__title">Install</h3><ul class="task__list"><li><span class="hex"></span>Mulch</li><li><span class="hex"></span>DG</li><li><span class="hex"></span>Plants</li><li><span class="hex"></span>Rock</li></ul></div>
    <div class="task" style="left:359px"><h3 class="task__title">Maintenance &amp; Other</h3><ul class="task__list"><li><span class="hex"></span>Yard cleanup</li><li><span class="hex"></span>Weed prevention (pre-emergent)</li><li><span class="hex"></span>Roof &amp; gutter cleaning</li><li><span class="hex"></span>Fence &amp; deck staining</li></ul></div>
    <p class="ask">DON’T SEE? JUST ASK!</p>

    <div class="photo photo--haul" role="img" aria-label="Black and white photo of a worker hauling brush in a wheelbarrow"></div>
    <div class="photo photo--rake" role="img" aria-label="Black and white photo of a rake gathering fallen leaves"></div>
    <div class="photo photo--saw" role="img" aria-label="Black and white photo of a worker cutting a fallen branch with a chainsaw"></div>

    <h2 class="label label--why">Why Choose Us?</h2>
    <ul class="why"><li><span class="hex"></span>Locally owned since 2022</li><li><span class="hex"></span>Reliable &amp; affordable – no corners cut</li><li><span class="hex"></span>Professional results you can trust</li></ul>

    <p class="licensed">Licensed and Insured</p>
    <p class="perks">Quality work <span class="dot"></span> On Time <span class="dot"></span> References <span class="dot"></span> Flexible <span class="dot"></span> Follow-up</p>

    <footer class="footer">
      <p class="footer__cta">Call or Text Today!</p>
      <div class="contacts">
        <span class="contact"><svg viewBox="0 0 16 16"><circle cx="8" cy="8" r="6.5"/><ellipse cx="8" cy="8" rx="3" ry="6.5"/><path d="M1.5 8h13M2.5 4.5h11M2.5 11.5h11"/></svg>www.brackwellyard.example</span>
        <span class="contact"><svg viewBox="0 0 16 16"><rect x="1.5" y="3.5" width="13" height="9"/><path d="M1.5 3.5 8 9l6.5-5.5"/></svg>sales@brackwellyard.example</span>
        <span class="contact"><svg viewBox="0 0 16 16"><path d="M4 1.5 6 4.5 4.8 6a8 8 0 0 0 5.2 5.2L11.5 10l3 2-1.5 2.2C7.5 14 2 8.5 1.8 3z"/></svg>(555) 014-7293</span>
      </div>
    </footer>
  </section>
</body>
</html>
```